Sandwich Board and Poster design promoting a medical aesthetic clinic

I am looking for a clean, modern and relaxing design promoting a medical physician-led aesthetic clinic.
Services offered are neuromodulator treatment (Dyneline) and Dermal Fillers.
Logo must be included.
Use the tag line "Refresh your look, revive your spirit."
Address is 204-205 27361 93 Ave, Surrey, K7P 2R4
604-555-0172
email - info@brightmoorskin.ca
www.brightmoorskin.ca

```html
<!DOCTYPE html>
<html lang="en">
<head>
<meta charset="utf-8">
<title>Brightmoor Skin – Sandwich Board Poster</title>
<link rel="stylesheet" href="https://fonts.googleapis.com/css2?family=Montserrat:wght@300;500;800&family=Poppins:wght@500;600;700;800&family=Oswald:wght@300&family=Kaushan+Script&display=swap">
<style>
  :root {
    --page-bg: #e8e6e2;
    --poster-bg: #fbfbfb;
    --ink: #1d1d1d;
    --gold: #b8962a;
    --gold-light: #c9a636;
    --rule: #b9b9b9;
    --skin-light: #e9c9b3;
    --skin-mid: #cfa085;
    --skin-dark: #8a6552;
    --hair: #3a2c26;
    --glove: #7ea6dc;
  }
  * { box-sizing: border-box; margin: 0; padding: 0; }
  html, body { width: 1200px; height: 861px; overflow: hidden; background: var(--page-bg); }
  .poster {
    position: absolute; left: 278px; top: 15px;
    width: 643px; height: 830px;
    background: var(--poster-bg);
    overflow: hidden;
    box-shadow: 0 2px 10px rgba(0,0,0,.12);
    font-family: "Montserrat", sans-serif;
    color: var(--ink);
  }
  .hero-photo {
    position: absolute; left: 0; top: 0; width: 380px; height: 830px;
    background:
      linear-gradient(180deg, var(--hair) 0%, rgba(58,44,38,0) 12%),
      linear-gradient(100deg, var(--skin-light) 0%, var(--skin-mid) 45%, var(--skin-light) 70%, rgba(251,251,251,0) 100%);
  }
  .treatment-grid .tile {
    position: absolute; border-radius: 18px; border: 3px solid #fff;
    box-shadow: 0 1px 4px rgba(0,0,0,.15);
  }
  .tile-1 { left: 67px; top: 513px; width: 110px; height: 99px; background: linear-gradient(135deg, #d9c4b6, var(--skin-mid) 60%, var(--hair)); }
  .tile-2 { left: 184px; top: 506px; width: 109px; height: 148px; background: linear-gradient(160deg, var(--glove) 0%, var(--skin-mid) 50%, var(--skin-dark)); }
  .tile-3 { left: 57px; top: 615px; width: 113px; height: 152px; background: linear-gradient(120deg, #f1dfd2, var(--skin-light) 50%, var(--glove)); }
  .tile-4 { left: 173px; top: 661px; width: 113px; height: 113px; background: linear-gradient(150deg, #f2ece8, var(--skin-light) 45%, var(--glove)); }

  .brand { position: absolute; left: 340px; width: 290px; top: 28px; text-align: center; }
  .brand-mark { display: block; margin: 0 auto 10px; }
  .brand-name { font-weight: 500; font-size: 17px; letter-spacing: 4px; color: var(--ink); }

  .headline { position: absolute; left: 340px; width: 280px; top: 186px; text-align: center; }
  .headline-refresh { font-family: "Oswald", sans-serif; font-weight: 300; font-size: 40px; color: var(--gold); line-height: 1; }
  .headline-look { font-family: "Poppins", sans-serif; font-weight: 800; font-size: 60px; line-height: .95; letter-spacing: -1px; }
  .headline-revive { font-family: "Kaushan Script", cursive; font-size: 32px; color: var(--gold); line-height: .8; margin-top: -8px; position: relative; }
  .headline-spirit { font-weight: 300; font-size: 43px; line-height: 1; letter-spacing: 1px; }

  .divider { position: absolute; left: 330px; width: 285px; border-top: 1px dashed var(--rule); }
  .divider-top { top: 462px; }
  .divider-bottom { top: 628px; }

  .services { position: absolute; left: 332px; top: 474px; width: 290px; }
  .services-kicker { font-weight: 300; font-size: 26px; letter-spacing: 2px; color: var(--gold); line-height: 1; }
  .services-title { font-weight: 800; font-size: 26px; letter-spacing: 1px; color: var(--gold); line-height: 1.05; }
  .service-list { list-style: none; margin-top: 12px; font-family: "Poppins", sans-serif; font-weight: 600; font-size: 16px; line-height: 1.2; }
  .service-list li { display: flex; gap: 10px; margin-bottom: 9px; }
  .service-list svg { flex: none; margin-top: 3px; }

  .contact { position: absolute; left: 332px; top: 642px; width: 295px; list-style: none; font-family: "Poppins", sans-serif; font-weight: 500; font-size: 13.5px; line-height: 1.25; }
  .contact li { display: flex; gap: 12px; margin-bottom: 12px; }
  .contact svg { flex: none; margin-top: 1px; }
  .website { position: absolute; left: 332px; top: 762px; font-family: "Poppins", sans-serif; font-weight: 700; font-size: 20px; color: var(--gold); }
</style>
</head>
<body>
<main class="poster">
  <div class="hero-photo" role="img" aria-label="Photo of two women in side profile with smooth, glowing skin"></div>

  <div class="treatment-grid">
    <div class="tile tile-1" role="img" aria-label="Photo of a forehead injection treatment"></div>
    <div class="tile tile-2" role="img" aria-label="Photo of a gloved hand injecting near the eye"></div>
    <div class="tile tile-3" role="img" aria-label="Photo of a client receiving a brow injection"></div>
    <div class="tile tile-4" role="img" aria-label="Photo of a lip filler treatment"></div>
  </div>

  <header class="brand">
    <svg class="brand-mark" width="40" height="40" viewBox="0 0 40 40" aria-hidden="true">
      <circle cx="20" cy="20" r="18" fill="none" stroke="var(--gold)" stroke-width="2"/>
    </svg>
    <div class="brand-name">BRIGHTMOOR SKIN</div>
  </header>

  <h1 class="headline">
    <div class="headline-refresh">REFRESH</div>
    <div class="headline-look">YOUR<br>LOOK</div>
    <div class="headline-revive">revive</div>
    <div class="headline-spirit">YOUR<br>SPIRIT</div>
  </h1>

  <div class="divider divider-top"></div>

  <section class="services">
    <div class="services-kicker">SERVICES</div>
    <div class="services-title">WE OFFER</div>
    <ul class="service-list">
      <li>
        <svg width="14" height="14" viewBox="0 0 14 14" aria-hidden="true"><circle cx="7" cy="7" r="7" fill="var(--ink)"/><path d="M3.8 7.2l2.1 2 4.3-4.4" fill="none" stroke="#fff" stroke-width="1.8"/></svg>
        <span>Neuromodulator<br>Treatment (Dyneline)</span>
      </li>
      <li>
        <svg width="14" height="14" viewBox="0 0 14 14" aria-hidden="true"><circle cx="7" cy="7" r="7" fill="var(--ink)"/><path d="M3.8 7.2l2.1 2 4.3-4.4" fill="none" stroke="#fff" stroke-width="1.8"/></svg>
        <span>Dermal Fillers</span>
      </li>
    </ul>
  </section>

  <div class="divider divider-bottom"></div>

  <ul class="contact">
    <li>
      <svg width="13" height="17" viewBox="0 0 13 17" aria-hidden="true"><path d="M6.5 0A6.5 6.5 0 0 0 0 6.5C0 11 6.5 17 6.5 17S13 11 13 6.5A6.5 6.5 0 0 0 6.5 0z" fill="var(--gold)"/><circle cx="6.5" cy="6.5" r="2.5" fill="#fff"/></svg>
      <span>204-205 27361 93 Ave, Surrey,<br>K7P 2R4</span>
    </li>
    <li>
      <svg width="14" height="14" viewBox="0 0 24 24" aria-hidden="true"><path d="M6.6 10.8a15.1 15.1 0 0 0 6.6 6.6l2.2-2.2a1 1 0 0 1 1-.25 11.4 11.4 0 0 0 3.6.57 1 1 0 0 1 1 1V20a1 1 0 0 1-1 1A17 17 0 0 1 3 4a1 1 0 0 1 1-1h3.5a1 1 0 0 1 1 1c0 1.25.2 2.45.57 3.57a1 1 0 0 1-.25 1z" fill="var(--gold)"/></svg>
      <span>604-555-0172</span>
    </li>
    <li>
      <svg width="14" height="11" viewBox="0 0 14 11" aria-hidden="true"><rect width="14" height="11" rx="1" fill="var(--gold)"/><path d="M0.5 1l6.5 5 6.5-5" fill="none" stroke="#fff" stroke-width="1.2"/></svg>
      <span>info@brightmoorskin.ca</span>
    </li>
  </ul>

  <div class="website">www.brightmoorskin.ca</div>
</main>
</body>
</html>
```